Home Security Company Business Card

Looking for a eye catching business card that is non traditional and stands out but yet still looks professional. It should include all the pertinent information such as name, title, address, telephone, e-mail, website address should definitely stand out and then finally the logo.

Target Market(s)

Residential and Commercial accounts mostly upscale accounts

Industry/Entity Type

Security

Contact Information for Business Card

Name
Title
Address
Office #
Cell #
E-mail
Website

Font styles to use
Serif
Sans Serif

Requirements
Must have
• Logo, two sided color configuration
Nice to have
• You decide
Should not have
• There really aren't any.

```html
<!DOCTYPE html>
<html lang="en">
<head>
<meta charset="utf-8">
<title>Harborline Protection Group – Business Card</title>
<link href="https://fonts.googleapis.com/css2?family=Open+Sans:wght@400;600;700&display=swap" rel="stylesheet">
<style>
  :root {
    --maroon: #7a1f2b;
    --gold: #e3a92f;
    --ink: #5a1620;
    --paper: #ffffff;
    --backdrop: #ece8e3;
  }
  * { box-sizing: border-box; margin: 0; padding: 0; }
  html, body { width: 1200px; height: 913px; overflow: hidden; }
  body {
    background: var(--backdrop);
    font-family: "Open Sans", Arial, sans-serif;
    color: var(--maroon);
    position: relative;
  }
  .card {
    position: absolute;
    width: 560px;
    height: 320px;
    background: var(--paper);
    box-shadow: 0 6px 18px rgba(60, 30, 20, 0.18);
    overflow: hidden;
  }
  .card--front { left: 70px; top: 90px; }
  .card--back { left: 570px; top: 500px; }

  .brand {
    position: absolute;
    display: flex;
    align-items: center;
    gap: 12px;
  }
  .brand__dot {
    width: 34px; height: 34px;
    border-radius: 50%;
    background: var(--gold);
  }
  .brand__name {
    font-weight: 600;
    font-size: 20px;
    letter-spacing: 0.5px;
    color: var(--maroon);
    line-height: 1.1;
  }
  .card--front .brand { left: 200px; top: 40px; }
  .card--back .brand { left: 50%; top: 95px; transform: translateX(-50%); }
  .card--back .brand__dot { width: 44px; height: 44px; }
  .card--back .brand__name { font-size: 24px; }

  .contacts {
    position: absolute;
    right: 36px; top: 108px;
    list-style: none;
    text-align: right;
    font-size: 14px;
    line-height: 22px;
    color: var(--ink);
  }
  .contacts li { display: flex; justify-content: flex-end; align-items: center; gap: 8px; }
  .contacts svg { width: 12px; height: 12px; fill: none; stroke: var(--gold); stroke-width: 1.6; }

  .holder {
    position: absolute;
    left: 40px; top: 188px; right: 36px;
    display: flex;
    align-items: flex-end;
    gap: 10px;
  }
  .holder__name { font-weight: 700; font-size: 22px; color: var(--maroon); white-space: nowrap; }
  .holder__rule { flex: 1; height: 1.5px; background: var(--maroon); margin-bottom: 8px; }
  .holder__title {
    position: absolute;
    left: 40px; top: 218px;
    font-size: 13px; color: var(--gold);
  }
  .accent-disc {
    position: absolute;
    left: -26px; top: 196px;
    width: 52px; height: 52px;
    border-radius: 50%;
    background: var(--gold);
  }
  .address {
    position: absolute;
    left: 40px; top: 252px;
    font-style: normal;
    font-size: 15px;
    line-height: 21px;
    color: var(--ink);
  }

  .back__rule {
    position: absolute;
    left: 60px; right: 60px; top: 190px;
    height: 1.5px;
    background: var(--gold);
  }
  .website {
    position: absolute;
    left: 0; right: 0; top: 208px;
    text-align: center;
    font-weight: 700;
    font-size: 16px;
    color: var(--ink);
  }
</style>
</head>
<body>
  <section class="card card--front" aria-label="Card front">
    <div class="brand">
      <span class="brand__dot"></span>
      <span class="brand__name">Harborline Protection Group</span>
    </div>
    <ul class="contacts">
      <li>+330 5550-1427
        <svg viewBox="0 0 12 12"><path d="M2 2h3l1 2.5-1.5 1a6 6 0 0 0 2.5 2.5l1-1.5L10.5 7.5v3A8.5 8.5 0 0 1 1.5 2.5z"/></svg>
      </li>
      <li>+330 5550-38214
        <svg viewBox="0 0 12 12"><rect x="3.5" y="1" width="5" height="10" rx="1"/><path d="M5.5 9.5h1"/></svg>
      </li>
      <li>info@marcuswhitfieldmail.com
        <svg viewBox="0 0 12 12"><rect x="1" y="2.5" width="10" height="7" rx="0.8"/><path d="M1 3l5 3.5L11 3"/></svg>
      </li>
    </ul>
    <span class="accent-disc"></span>
    <div class="holder">
      <span class="holder__name">Marcus Whitfield</span>
      <span class="holder__rule"></span>
    </div>
    <span class="holder__title">Owner</span>
    <address class="address">742 Alder Lane<br>Brookfield, Ohio 44403</address>
  </section>

  <section class="card card--back" aria-label="Card back">
    <div class="brand">
      <span class="brand__dot"></span>
      <span class="brand__name">Harborline Protection Group</span>
    </div>
    <span class="back__rule"></span>
    <p class="website">www.harborlineprotection.com</p>
  </section>
</body>
</html>
```